Business Card for a mobile physiotherapy company

I need a layout for a business card for a mobile physiotherapy company.
Slogan is "Mobile Physiotherapy - Your Road To Recovery"
Phone number is 867-555-0142
Email VardenTherapy@postnest.ca (subject to change with website)
Website www.VardenTherapy.ca
My name and credentials: Luke Varden Luke Varden, BSc(kin), MPT, CAFCI, IMS
Information maybe included: Direct Billing, Services including Physiotherapy, IMS, acupuncture
Maybe include facebook and instagram logos
One side with the logo clean and sharp
Other side with details, try not to look too busy, keep everything concise

```html
<!DOCTYPE html>
<html lang="en">
<head>
<meta charset="utf-8">
<title>Varden Therapy – Business Card</title>
<link href="https://fonts.googleapis.com/css2?family=Roboto:ital,wght@0,400;0,500;0,700;1,400&display=swap" rel="stylesheet">
<style>
  :root {
    --navy: #2c4a78;
    --green: #0f5647;
    --grey-text: #555555;
    --rule: #d6d6d6;
    --card: #ffffff;
    --backdrop: #efeeec;
  }
  * { margin: 0; padding: 0; box-sizing: border-box; }
  html, body {
    width: 1125px;
    height: 1200px;
    overflow: hidden;
    background: var(--backdrop);
    font-family: "Roboto", Arial, sans-serif;
  }
  .stage { position: relative; width: 1125px; height: 1200px; }
  .card {
    position: absolute;
    left: 171px;
    width: 826px;
    height: 471px;
    background: var(--card);
    box-shadow: 0 2px 6px rgba(0,0,0,0.18);
  }
  .card--front { top: 106px; }
  .card--back { top: 639px; }

  .social {
    position: absolute;
    top: 146px;
    right: 42px;
    display: flex;
    gap: 5px;
  }
  .social__dot {
    width: 38px; height: 38px;
    border-radius: 50%;
    background: var(--navy);
  }

  .identity {
    position: absolute;
    right: calc(826px - 376px);
    top: 186px;
    text-align: right;
  }
  .identity__name {
    font-weight: 700;
    font-size: 31px;
    line-height: 34px;
    color: var(--navy);
    letter-spacing: 0.2px;
  }
  .identity__creds {
    font-weight: 500;
    font-size: 19px;
    line-height: 24px;
    color: var(--navy);
  }
  .identity__billing {
    font-weight: 500;
    font-size: 20px;
    line-height: 26px;
    color: var(--green);
  }

  .divider {
    position: absolute;
    left: 414px;
    top: 188px;
    width: 1px;
    height: 98px;
    background: var(--rule);
  }

  .contact {
    position: absolute;
    left: 448px;
    top: 196px;
    list-style: none;
  }
  .contact__item {
    display: flex;
    align-items: center;
    height: 26px;
    font-size: 20px;
    color: var(--grey-text);
  }
  .contact__icon {
    width: 18px; height: 18px;
    margin-right: 12px;
    fill: var(--navy);
    flex: none;
  }

  .tagline {
    position: absolute;
    left: 0; right: 0;
    top: 374px;
    text-align: center;
  }
  .tagline__slogan {
    font-style: italic;
    font-size: 19.5px;
    line-height: 27px;
    color: var(--grey-text);
  }
  .tagline__services {
    font-size: 20px;
    line-height: 28px;
    color: var(--green);
  }
  .tagline__sep { font-size: 12px; vertical-align: 2px; margin: 0 3px; }

  .brand {
    position: absolute;
    left: 0; right: 0;
    top: 0; bottom: 0;
    display: flex;
    align-items: center;
    justify-content: center;
  }
  .brand__name {
    font-weight: 700;
    font-size: 46px;
    letter-spacing: 8px;
    color: var(--green);
    text-transform: uppercase;
  }
</style>
</head>
<body>
<div class="stage">

  <section class="card card--front" aria-label="Business card, details side">
    <div class="social" aria-label="Social media">
      <span class="social__dot"></span>
      <span class="social__dot"></span>
    </div>

    <div class="identity">
      <h1 class="identity__name">LUKE VARDEN</h1>
      <p class="identity__creds">BSc(kin), MPT, CAFCI, IMS</p>
      <p class="identity__billing">Direct Billing</p>
    </div>

    <div class="divider"></div>

    <ul class="contact">
      <li class="contact__item">
        <svg class="contact__icon" viewBox="0 0 24 24" aria-hidden="true"><path d="M6.6 10.8a15.1 15.1 0 0 0 6.6 6.6l2.2-2.2a1 1 0 0 1 1-.25 11.4 11.4 0 0 0 3.6.57 1 1 0 0 1 1 1V20a1 1 0 0 1-1 1A17 17 0 0 1 3 4a1 1 0 0 1 1-1h3.5a1 1 0 0 1 1 1c0 1.25.2 2.45.57 3.57a1 1 0 0 1-.25 1z"/></svg>
        867-555-0142
      </li>
      <li class="contact__item">
        <svg class="contact__icon" viewBox="0 0 24 24" aria-hidden="true"><path d="M3 6h18v12H3z M4.5 7.5v.3l7.5 5 7.5-5v-.3z M4.5 9.6v6.9h15V9.6L12 14.6z" fill-rule="evenodd"/></svg>
        VardenTherapy@postnest.ca
      </li>
      <li class="contact__item">
        <svg class="contact__icon" viewBox="0 0 24 24" aria-hidden="true"><path d="M12 2a10 10 0 1 0 0 20 10 10 0 0 0 0-20zm-1 17.9A8 8 0 0 1 4.2 10.2L9 15v1a2 2 0 0 0 2 2zm6.9-2.5A2 2 0 0 0 16 16h-1v-3a1 1 0 0 0-1-1H8v-2h2a1 1 0 0 0 1-1V7h2a2 2 0 0 0 2-2v-.4a8 8 0 0 1 2.9 12.8z"/></svg>
        www.VardenTherapy.ca
      </li>
    </ul>

    <div class="tagline">
      <p class="tagline__slogan">Mobile Physiotherapy - Your Road To Recovery</p>
      <p class="tagline__services">Physiotherapy<span class="tagline__sep">&#9679;</span>IMS<span class="tagline__sep">&#9679;</span>Acupuncture</p>
    </div>
  </section>

  <section class="card card--back" aria-label="Business card, brand side">
    <div class="brand">
      <p class="brand__name">Varden Therapy</p>
    </div>
  </section>

</div>
</body>
</html>
```